Merrow Trade finance web design

We are a newly established business which provides invoice finance to Small Businesses in England and Wales.
Our approach is very much a funder where the small business owner can talk to the decision maker. We will guarantee on receipt of information, a decision within 24 hours.
We are not a bank so the look of the website need to be friendly but professional.
Have two types of people we are trying to attract to the website: 1) partners who are small business owners and 2) introducers who is accountants and commercial brokers who introduce us to the small businesses.
Currently no website, although domain has been reserved.
The design should be:
Professional
“Clean” Look
Designed to convey Trust and Authority.
Appeal to the small business owner.
Must incorporate:
Logo (attached)
Front page:Top tabs to other pages 1) About us 2) Services 3) Introducers 4) Contact us
Need picture and logo on page.
1) About us page- Room for talk about the company, the people and our critera.
2) Services page- We need for what invoice finance is, and 5 boxes for different services we will provide. (link on page to contact us)
3) Introducers page- We need a part for why become an introducer? Who we can help? Why we are different? (link on page to contact us)
4) Contact us page- Office address, email, tel and if possible a map and a contact me part which will email direct to us.
Text will be provided for the design, if we can see the setup of the website we will provide a part for each of the pages to support.
Styles we think convey the correct image:
www.dornelcapital.example
www.plivanlend.example
www.quorbacredit.example
Target Market(s)
Small business owners
Industry/Entity Type
Finance
Number of Pages Required
5+ page
Look and feel

```html
<!DOCTYPE html>
<html lang="en">
<head>
<meta charset="utf-8">
<title>Merrow Trade finance</title>
<link href="https://fonts.googleapis.com/css2?family=Raleway:wght@400;500;600;700&family=Open+Sans:wght@400;600&display=swap" rel="stylesheet">
<style>
:root{
  --red:#c0161f;
  --ink:#333;
  --text:#666;
  --light:#f2f2f2;
  --footer:#3a3a3a;
  --white:#fff;
  --ring:#d4d4d4;
}
*{box-sizing:border-box;margin:0;padding:0}
html,body{width:1200px;height:3614px;overflow:hidden}
body{font-family:"Open Sans",Arial,sans-serif;color:var(--text);background:var(--white);font-size:13px;line-height:1.6}
h1,h2,h3,h4,.brand,.nav a,.btn{font-family:"Raleway",Arial,sans-serif}
.container{width:886px;margin:0 auto;position:relative}
.btn{display:inline-block;background:var(--red);color:var(--white);text-decoration:none;font-weight:600;text-transform:uppercase;font-size:13px;letter-spacing:.5px;padding:0 20px;line-height:34px;white-space:nowrap}

/* header */
.site-header{height:72px;display:flex;align-items:center}
.site-header .container{display:flex;align-items:center;justify-content:space-between}
.brand{font-size:34px;font-weight:700;color:var(--red);letter-spacing:-.5px}
.brand-light{color:var(--white)}
.nav{display:flex;align-items:center;gap:30px}
.nav a{font-size:12px;font-weight:600;color:var(--ink);text-decoration:none;text-transform:uppercase}
.nav a.active{color:var(--red)}
.nav .login{border:1px solid var(--ink);padding:0 18px;line-height:32px}
.nav .signup{background:var(--red);color:var(--white);padding:0 20px;line-height:34px}

/* hero */
.hero{position:relative;height:543px;color:var(--white);text-align:center}
.hero-photo{position:absolute;inset:0;background:linear-gradient(115deg,#6d7379 0%,#3c4146 40%,#1f2326 75%,#2f3337 100%)}
.hero-inner{position:absolute;top:188px;left:0;right:0}
.hero h1{font-size:46px;font-weight:400;letter-spacing:.5px}
.hero p{font-size:17px;line-height:1.45;width:620px;margin:20px auto 28px}
.hero .btn{font-size:17px;line-height:48px;padding:0 28px}
.hero .btn svg{vertical-align:-4px;margin-right:8px}
.slider-dots{position:absolute;top:484px;left:0;right:0;display:flex;justify-content:center;gap:10px}
.slider-dots span{width:32px;height:4px;background:var(--white);opacity:.85}
.slider-dots span.on{background:var(--red);opacity:1}

/* how it works */
.how{background:var(--light);height:445px;text-align:center;padding-top:56px}
.section-title{font-size:25px;font-weight:600;color:var(--ink)}
.how .intro{font-size:12px;width:560px;margin:12px auto 0;line-height:1.6}
.steps{display:flex;justify-content:space-between;width:820px;margin:44px auto 0;position:relative}
.step{width:200px;position:relative}
.step h4{font-size:14px;font-weight:700;color:var(--ink);margin-top:16px}
.step p{font-size:12px;margin-top:8px;line-height:1.5}
.step-ring{display:block;margin:0 auto}
.step-links{position:absolute;top:0;left:0}

/* features */
.features{padding-top:65px;height:1340px}
.feature{display:flex;justify-content:space-between;align-items:flex-start;margin-bottom:72px;height:250px}
.feature.reverse{flex-direction:row-reverse}
.feature-media{width:362px;height:246px;border:1px solid #e4e4e4;box-shadow:0 2px 6px rgba(0,0,0,.12);background:linear-gradient(90deg,#4a4a4a 0 78px,#f6f6f6 78px,#e9ecef 100%)}
.feature-body{width:484px;padding-top:2px}
.feature-body h3{font-size:21px;font-weight:500;color:var(--ink);line-height:1.3}
.feature-body p{font-size:11.5px;line-height:1.75;margin:14px 0 20px}
.feature-body .btn{font-size:12px;line-height:36px;padding:0 18px}

/* grow band */
.grow{position:relative;height:485px;color:var(--white);text-align:center;padding-top:50px}
.grow-bg{position:absolute;inset:0;background:linear-gradient(180deg,#2a2d30 0%,#3a3e42 55%,#2b2e31 100%)}
.grow .container{z-index:1}
.grow h2{font-size:25px;font-weight:700}
.grow .intro{font-size:12px;width:840px;margin:12px auto 0;line-height:1.6}
.grow-cards{display:flex;justify-content:space-between;margin-top:26px;text-align:left}
.grow-card{width:273px}
.grow-photo{height:186px}
.grow-card p{font-size:15px;line-height:1.4;margin-top:22px}

/* partners */
.partners{height:250px;text-align:center;padding-top:45px}
.partners h2{font-size:25px;font-weight:500;color:#555}
.partner-row{display:flex;justify-content:space-between;align-items:center;width:860px;margin:30px auto 0}
.partner-row + .partner-row{margin-top:26px}
.partner{font-family:"Raleway",Arial,sans-serif;font-size:16px;font-weight:700;color:#b5b5b5;white-space:nowrap}

/* signup */
.cta{height:147px;text-align:center;border-top:1px solid #eee;padding-top:35px}
.cta h2{font-size:25px;font-weight:600;color:#444}
.cta .btn{margin-top:16px;font-size:12px;line-height:36px}

/* footer */
.site-footer{background:var(--footer);height:241px;color:#ccc}
.site-footer .container{display:flex;height:100%}
.support{width:265px;border-right:1px solid #555;text-align:center;padding-top:36px;color:var(--white)}
.support h4{font-size:13px;font-weight:700;text-transform:uppercase;margin-top:2px}
.support .phone{font-family:"Raleway",Arial,sans-serif;font-size:22px;font-weight:700;line-height:1.3;white-space:nowrap}
.support .hours{font-size:12px;font-weight:600}
.support .mail{font-size:12px;font-weight:600;margin-top:12px;line-height:1.6}
.footer-cols{display:flex;padding:40px 0 0 43px}
.footer-col{width:160px}
.footer-col h4{font-size:13px;font-weight:700;color:var(--white);text-transform:uppercase;margin-bottom:8px}
.footer-col li{list-style:none;font-size:12px;line-height:1.75}

/* bottom bar */
.bottom-bar{background:var(--red);height:91px;color:var(--white)}
.bottom-bar .container{display:flex;justify-content:space-between;align-items:center;height:100%}
.bottom-bar small{font-size:11px;line-height:1.7;display:block}
.bottom-right{display:flex;align-items:center;gap:10px}
.social{width:28px;height:28px;border:2px solid var(--white);border-radius:50%}
.bottom-right .brand{font-size:30px;margin-right:6px}
</style>
</head>
<body>

<header class="site-header">
  <div class="container">
    <div class="brand">Merrow</div>
    <nav class="nav">
      <a href="#" class="active">Home</a>
      <a href="#">About us</a>
      <a href="#">Services</a>
      <a href="#">Introducers</a>
      <a href="#">Contact us</a>
      <a href="#" class="login">Login</a>
      <a href="#" class="signup">Sign up</a>
    </nav>
  </div>
</header>

<section class="hero">
  <div class="hero-photo" role="img" aria-label="Business person reviewing financial charts on a tablet"></div>
  <div class="hero-inner">
    <h1>We Offer Financing Solutions</h1>
    <p>Sed ut perspiciatis unde omnis iste natus error sit voluptatem accusantiumdol orem que laudantium, totam rem aperiam, eaque ipsa quae ab ill</p>
    <a class="btn" href="#"><svg width="18" height="18" viewBox="0 0 18 18"><circle cx="9" cy="9" r="9" fill="#fff"/><path d="M7 5l5 4-5 4z" fill="#c0161f"/></svg>Get started here</a>
  </div>
  <div class="slider-dots"><span></span><span></span><span class="on"></span><span></span></div>
</section>

<section class="how">
  <h2 class="section-title">How Does Merrow Trade finance Funding Work?</h2>
  <p class="intro">Sed ut perspiciatis unde omnis iste natus error sit voluptatem accusantium doloremque laudantium, totam rem aperiam, eaque ipsa quae ab illo inventore veritatis et quasi architecto beatae vitae dicta sunt explicabo.</p>
  <div class="steps">
    <svg class="step-links" width="820" height="110" viewBox="0 0 820 110" aria-hidden="true">
      <path d="M160 45 Q210 20 260 50" fill="none" stroke="#d8d8d8" stroke-width="1.5" stroke-dasharray="4 4"/>
      <path d="M394 60 Q444 85 494 55" fill="none" stroke="#d8d8d8" stroke-width="1.5" stroke-dasharray="4 4"/>
      <path d="M628 45 Q678 20 728 50" fill="none" stroke="#d8d8d8" stroke-width="1.5" stroke-dasharray="4 4"/>
    </svg>
    <div class="step">
      <svg class="step-ring" width="110" height="110" viewBox="0 0 110 110">
        <circle cx="55" cy="55" r="49" fill="#fff" stroke="#d4d4d4" stroke-width="10"/>
        <path d="M55 6 A49 49 0 0 0 6 55" fill="none" stroke="#c0161f" stroke-width="10"/>
        <rect x="40" y="42" width="30" height="20" rx="2" fill="none" stroke="#c0161f" stroke-width="3"/>
        <rect x="49" y="64" width="12" height="4" fill="#c0161f"/>
      </svg>
      <h4>Finibus Bonorum</h4>
      <p>Sed ut perspiciatis unde omnisnat serror sit voluptatem accusantiumd oremque laudantium, totam re.</p>
    </div>
    <div class="step">
      <svg class="step-ring" width="110" height="110" viewBox="0 0 110 110">
        <circle cx="55" cy="55" r="49" fill="#fff" stroke="#d4d4d4" stroke-width="10"/>
        <path d="M55 6 A49 49 0 0 1 104 55" fill="none" stroke="#c0161f" stroke-width="10"/>
        <path d="M40 53h7v17h-7z M50 53l7-12c3 0 4 2 3 5l-1 5h9c2 0 3 2 2 4l-3 12c-1 2-2 3-4 3H50z" fill="#c0161f"/>
      </svg>
      <h4>Finibus Bonorum</h4>
      <p>Sed ut perspiciatis unde omnisnat serror sit voluptatem accusantiumd oremque laudantium, totam re.</p>
    </div>
    <div class="step">
      <svg class="step-ring" width="110" height="110" viewBox="0 0 110 110">
        <circle cx="55" cy="55" r="49" fill="#fff" stroke="#d4d4d4" stroke-width="10"/>
        <path d="M104 55 A49 49 0 0 1 55 104" fill="none" stroke="#c0161f" stroke-width="10"/>
        <circle cx="55" cy="55" r="11" fill="none" stroke="#c0161f" stroke-width="7" stroke-dasharray="5 3.6"/>
        <circle cx="55" cy="55" r="4" fill="#c0161f"/>
      </svg>
      <h4>Finibus Bonorum</h4>
      <p>Sed ut perspiciatis unde omnisnat serror sit voluptatem accusantiumd oremque laudantium, totam re.</p>
    </div>
    <div class="step">
      <svg class="step-ring" width="110" height="110" viewBox="0 0 110 110">
        <circle cx="55" cy="55" r="49" fill="#fff" stroke="#d4d4d4" stroke-width="10"/>
        <path d="M6 55 A49 49 0 0 0 104 55" fill="none" stroke="#c0161f" stroke-width="10"/>
        <rect x="38" y="45" width="34" height="20" rx="2" fill="none" stroke="#c0161f" stroke-width="3"/>
        <circle cx="55" cy="55" r="5" fill="#c0161f"/>
      </svg>
      <h4>Finibus Bonorum</h4>
      <p>Sed ut perspiciatis unde omnisnat serror sit voluptatem accusantiumd oremque laudantium, totam re.</p>
    </div>
  </div>
</section>

<section class="features">
  <div class="container">

    <article class="feature">
      <div class="feature-media" role="img" aria-label="Screenshot of a finance dashboard with area charts and progress gauges"></div>
      <div class="feature-body">
        <h3>Accounts Receivable Financing Companies<br>Compete all in One Place</h3>
        <p>Sed ut perspiciatis unde omnis iste natus error sit voluptatem accusantium doloremque laudantium, totam rem aperiam, eaque ipsa quae ab illo inventore veritatis et quasi architecto beatae vitae dicta sunt explicabo. Nemo enim ipsam voluptatem quia voluptas sit aspernatur aut odit aut fugit, sed quia consequuntur magni dolores eos qui ratione voluptatem sequi nesciunt.eque porro quisquam est, qui dolorem ipsum quia dolor sit amet, consectetur, adipisci velit, sed quia non numquam eius modi tempora incidunt ut labore et dolore magnam ipsum quia dolor sit amet, consectetur, adipisci velit, sed quia non numquam eius modi tempora incidunt ut labore et dolore magnam.</p>
        <a class="btn" href="#">Read more</a>
      </div>
    </article>

    <article class="feature reverse">
      <div class="feature-media" role="img" aria-label="Screenshot of a finance dashboard with line charts"></div>
      <div class="feature-body">
        <h3>Offers from Factoring Companies<br>What deals are realistic for your business</h3>
        <p>Sed ut perspiciatis unde omnis iste natus error sit voluptatem accusantium doloremque laudantium, totam rem aperiam, eaque ipsa quae ab illo inventore veritatis et quasi architecto beatae vitae dicta sunt explicabo. Nemo enim ipsam voluptatem quia voluptas sit aspernatur aut odit aut fugit, sed quia consequuntur magni dolores eos qui ratione voluptatem sequi nesciunt.eque porro quisquam est, qui dolorem ipsum quia dolor sit amet, consectetur, adipisci velit, sed quia non numquam eius modi tempora incidunt ut labore et dolore magnam ipsum quia dolor sit amet, consectetur, adipisci velit, sed quia non numquam eius modi tempora incidunt ut labore et dolore magnam.</p>
        <a class="btn" href="#">Read more</a>
      </div>
    </article>

    <article class="feature">
      <div class="feature-media" role="img" aria-label="Screenshot of a finance dashboard with stacked bar charts"></div>
      <div class="feature-body">
        <h3>Your Factoring Discount Rate Aspects that<br>influence your company and clients' risk</h3>
        <p>Sed ut perspiciatis unde omnis iste natus error sit voluptatem accusantium doloremque laudantium, totam rem aperiam, eaque ipsa quae ab illo inventore veritatis et quasi architecto beatae vitae dicta sunt explicabo. Nemo enim ipsam voluptatem quia voluptas sit aspernatur aut odit aut fugit, sed quia consequuntur magni dolores eos qui ratione voluptatem sequi nesciunt.eque porro quisquam est, qui dolorem ipsum quia dolor sit amet, consectetur, adipisci velit, sed quia non numquam eius modi tempora incidunt ut labore et dolore magnam ipsum quia dolor sit amet, consectetur, adipisci velit, sed quia non numquam eius modi tempora incidunt ut labore et dolore magnam.</p>
        <a class="btn" href="#">Read more</a>
      </div>
    </article>

    <article class="feature reverse">
      <div class="feature-media" role="img" aria-label="Screenshot of a finance dashboard with yearly bar chart"></div>
      <div class="feature-body">
        <h3>How Long the Factoring Application,<br>Approval &amp; Funding Process Really Takes?</h3>
        <p>Sed ut perspiciatis unde omnis iste natus error sit voluptatem accusantium doloremque laudantium, totam rem aperiam, eaque ipsa quae ab illo inventore veritatis et quasi architecto beatae vitae dicta sunt explicabo. Nemo enim ipsam voluptatem quia voluptas sit aspernatur aut odit aut fugit, sed quia consequuntur magni dolores eos qui ratione voluptatem sequi nesciunt.eque porro quisquam est, qui dolorem ipsum quia dolor sit amet, consectetur, adipisci velit, sed quia non numquam eius modi tempora incidunt ut labore et dolore magnam ipsum quia dolor sit amet, consectetur, adipisci velit, sed quia non numquam eius modi tempora incidunt ut labore et dolore magnam.</p>
        <a class="btn" href="#">Read more</a>
      </div>
    </article>

  </div>
</section>

<section class="grow">
  <div class="grow-bg" role="img" aria-label="Dimmed photo of business colleagues at a meeting table"></div>
  <div class="container">
    <h2>We Understand What it takes to Grow and Build a Business</h2>
    <p class="intro">Sed ut perspiciatis unde omnis iste natus error sit voluptatem accusantium doloremque laudantium, totam rem aperiam, eaque ipsa quae ab illo inventore veritatis et quasi architecto beatae vitae dicta sunt explicabo.ab illo inventore veritatis et quasi architecto beatae vitae dicta sunt explicabo.</p>
    <div class="grow-cards">
      <div class="grow-card">
        <div class="grow-photo" role="img" aria-label="Hands reviewing printed financial reports" style="background:linear-gradient(135deg,#9fb3c4,#5d7184)"></div>
        <p>Sed ut perspiciatis unde omnis tatem accusa ntiudoe laloren tium.</p>
      </div>
      <div class="grow-card">
        <div class="grow-photo" role="img" aria-label="Small business owners talking at a desk" style="background:linear-gradient(135deg,#c9a98a,#7a5c46)"></div>
        <p>Sed ut perspiciatis unde omnis tatem accusa ntiudoe laloren tium.</p>
      </div>
      <div class="grow-card">
        <div class="grow-photo" role="img" aria-label="Handshake over charts and paperwork" style="background:linear-gradient(135deg,#e1e6ea,#9aa7b2)"></div>
        <p>Sed ut perspiciatis unde omnis tatem accusa ntiudoe laloren tium.</p>
      </div>
    </div>
  </div>
</section>

<section class="partners">
  <h2>Integrates Seamlessly with most Accounting Software</h2>
  <div class="partner-row">
    <span class="partner">Orvale</span><span class="partner">Kestrel</span><span class="partner">Brindle</span><span class="partner">Tamsworth</span><span class="partner">Calloway</span><span class="partner">Veyra</span><span class="partner">Hollins &amp; Roe</span><span class="partner">Ledgerly</span>
  </div>
  <div class="partner-row">
    <span class="partner">Quintal</span><span class="partner">Pellmark</span><span class="partner">Strandway</span><span class="partner">Norvik</span><span class="partner">Corrabell</span><span class="partner">Fennick</span><span class="partner">Torrin</span><span class="partner">Halden Post</span>
  </div>
</section>

<section class="cta">
  <h2>Signing up takes just a few short minutes</h2>
  <a class="btn" href="#">Get started today</a>
</section>

<footer class="site-footer">
  <div class="container">
    <div class="support">
      <svg width="34" height="30" viewBox="0 0 34 30" aria-hidden="true"><path d="M4 2h18a3 3 0 0 1 3 3v9a3 3 0 0 1-3 3H12l-6 5v-5H4a3 3 0 0 1-3-3V5a3 3 0 0 1 3-3z" fill="#fff"/><path d="M27 9h3a3 3 0 0 1 3 3v8a3 3 0 0 1-3 3h-1v5l-6-5h-7v-3h7a4 4 0 0 0 4-4z" fill="#fff"/></svg>
      <h4>Support</h4>
      <div class="phone">+44 0161 555 0142</div>
      <div class="hours">8am - 8pm UTC</div>
      <div class="mail">support@merrowtrade.example<br>sales@merrowtrade.example</div>
    </div>
    <div class="footer-cols">
      <div class="footer-col"><h4>Resources</h4><ul><li>API</li><li>Mobile Apps</li><li>Downloads</li><li>Tutorials</li><li>FAQ</li></ul></div>
      <div class="footer-col"><h4>Product</h4><ul><li>Uptime</li><li>Performance</li><li>Transaction</li><li>Alerting</li><li>Page Speed</li><li>Pricing</li></ul></div>
      <div class="footer-col"><h4>Company</h4><ul><li>Why Merrow Trade</li><li>Contact</li><li>Brand Assets</li><li>Jobs</li><li>Customers</li></ul></div>
      <div class="footer-col"><h4>Links</h4><ul><li>Home</li><li>About us</li><li>Services</li><li>Introducers</li><li>Contact us</li></ul></div>
    </div>
  </div>
</footer>

<div class="bottom-bar">
  <div class="container">
    <div>
      <small>© 2016 Merrow Trade finance. All Copyrights are Reserved.</small>
      <small>Privacy | Terms &amp; Conditions</small>
    </div>
    <div class="bottom-right">
      <span class="brand brand-light">Merrow</span>
      <span class="social"></span><span class="social"></span><span class="social"></span><span class="social"></span>
    </div>
  </div>
</div>

</body>
</html>
```